BOLD & MINIMALIST DESIGN NEEDED

We want a very bold but minimalistic business card design that is impactful and utilizes both sides of the business card. Our current logo is included for your use.

We want bold fonts and good use of negative space. We don't want the logo to overpower the design.

Target Market(s)

Professionals who are building new commercial buildings.

Industry/Entity Type

Construction

Contact Information for Business Card

Name, Title, email, office phone, cell phone, website

Font styles to use
Serif
Sans Serif

Requirements
Must have
• Bold design!

```html
<!DOCTYPE html>
<html lang="en">
<head>
<meta charset="utf-8">
<title>Ridgeline Business Card</title>
<link rel="stylesheet" href="https://fonts.googleapis.com/css2?family=Red+Hat+Display:wght@400;500;900&family=Oswald:wght@300&display=swap">
<style>
  :root {
    --backdrop: #a3a3a3;
    --silver-light: #f1f3f4;
    --silver-mid: #d6dadd;
    --lime: #8cc63f;
    --lime-light: #a2d64c;
    --ink: #0b0b0b;
    --card-black: #141414;
    --white: #ffffff;
    --muted: #d9d9d9;
  }
  * { margin: 0; padding: 0; box-sizing: border-box; }
  html, body { width: 1200px; height: 1200px; overflow: hidden; }
  body {
    background: var(--backdrop);
    position: relative;
    font-family: "Red Hat Display", sans-serif;
  }
  .card {
    position: absolute;
    width: 686px;
    height: 392px;
    left: 261px;
    overflow: hidden;
  }
  .card-front {
    top: 165px;
    background: linear-gradient(125deg, var(--silver-mid) 0%, var(--silver-light) 45%, var(--silver-mid) 100%);
  }
  .card-back {
    top: 653px;
    background: linear-gradient(135deg, #1c1c1c 0%, var(--card-black) 55%, #262626 80%, #121212 100%);
  }
  .panel-shapes { position: absolute; inset: 0; }
  .brand {
    position: absolute;
    display: flex;
    align-items: center;
    gap: 12px;
    font-weight: 900;
    letter-spacing: 1px;
  }
  .brand-mark { width: 22px; height: 22px; background: var(--lime); }
  .card-front .brand {
    left: 0; width: 344px; top: 172px;
    justify-content: center;
    font-size: 38px; color: var(--ink);
  }
  .card-back .brand {
    left: 0; right: 0; top: 150px;
    justify-content: center;
    font-size: 52px; color: var(--white);
  }
  .card-back .brand-mark { width: 30px; height: 30px; }
  .holder-name {
    position: absolute; left: 382px; top: 64px;
    font-size: 25px; font-weight: 500; color: var(--ink); letter-spacing: 0.5px;
  }
  .holder-title {
    position: absolute; left: 382px; top: 98px;
    font-size: 17px; font-weight: 500; color: var(--white); letter-spacing: 0.5px;
  }
  .address {
    position: absolute; left: 386px; top: 234px;
    font-family: "Oswald", sans-serif; font-weight: 300;
    font-size: 14px; line-height: 19px; color: var(--muted);
  }
  .contact-list {
    position: absolute; left: 392px; top: 293px;
    list-style: none;
    font-size: 16px; line-height: 20px; color: var(--muted);
  }
  .contact-list li { display: flex; align-items: center; gap: 10px; }
  .contact-list svg { width: 13px; height: 13px; flex: none; }
  .back-web {
    position: absolute; left: 0; right: 0; top: 351px;
    text-align: center; font-size: 15px; font-weight: 500;
    letter-spacing: 4px; color: var(--lime);
  }
</style>
</head>
<body>

<section class="card card-front">
  <svg class="panel-shapes" viewBox="0 0 686 392" aria-hidden="true">
    <polygon points="344,30 413,0 686,0 686,111 344,208" fill="var(--lime-light)"/>
    <polygon points="344,208 686,111 686,116 344,214" fill="var(--white)"/>
    <polygon points="344,214 686,116 686,392 344,392" fill="var(--ink)"/>
  </svg>

  <div class="brand"><span class="brand-mark"></span>RIDGELINE</div>

  <h1 class="holder-name">DANIEL REYES</h1>
  <p class="holder-title">PRESIDENT</p>

  <p class="address">4120 BIRCHWOOD ROAD<br>JUNEAU, ALASKA 99801</p>

  <ul class="contact-list">
    <li>
      <svg viewBox="0 0 16 16"><path fill="var(--lime)" d="M3 1l3 1 1 4-2 1.5c1 2 2.5 3.5 4.5 4.5L11 10l4 1 1 3-2 2C7 16 0 9 0 3z"/></svg>
      555-240-7318
    </li>
    <li>
      <svg viewBox="0 0 16 16"><rect x="0" y="3" width="16" height="10" fill="var(--lime)"/><path d="M0 3l8 6 8-6" fill="none" stroke="var(--ink)" stroke-width="1.5"/></svg>
      INFO@RIDGELINEBUILD.COM
    </li>
    <li>
      <svg viewBox="0 0 16 16"><circle cx="8" cy="8" r="7.5" fill="var(--lime)"/><path d="M4 4q3 1 2 4t-1 5M10 3q-1 3 2 5" fill="none" stroke="var(--ink)" stroke-width="1.6"/></svg>
      WWW.RIDGELINEBUILD.COM
    </li>
  </ul>
</section>

<section class="card card-back">
  <div class="brand"><span class="brand-mark"></span>RIDGELINE</div>
  <p class="back-web">WWW.RIDGELINEBUILD.COM</p>
</section>

</body>
</html>
```